Calvanto Group Real Estate Company business cards

New business card design, we are generally happy with the basic layout of the existing front of business card, (feel free to change) but require a head shot photo on the back side.

http://www.calvanto.com.au/

Attached logos, and existing business card

------------------------------

Target Market(s)

Real estate

Industry/Entity Type

Real Estate

Contact Information for Business Card

Standard size double sided

Font styles to use
Other font styles liked:
• Futura

Requirements
Must have
• Photo head shot on the back side
Nice to have
• yes
Should not have
• No

```html
<!DOCTYPE html>
<html lang="en">
<head>
<meta charset="utf-8">
<title>Calvanto Group – Business Cards</title>
<link rel="stylesheet" href="https://fonts.googleapis.com/css2?family=Source+Sans+3:wght@400;600&display=swap">
<style>
  :root {
    --purple: #2d2160;
    --orange: #f7941d;
    --white: #ffffff;
    --paper: #ececef;
    --photo-light: #c9ccd3;
    --photo-dark: #5a6178;
  }
  * { margin: 0; padding: 0; box-sizing: border-box; }
  html, body { width: 1200px; height: 900px; overflow: hidden; }
  body {
    background: var(--paper);
    font-family: "Source Sans 3", "Myriad Pro", Arial, sans-serif;
    position: relative;
  }
  .card {
    position: absolute;
    overflow: hidden;
    box-shadow: 0 6px 18px rgba(0,0,0,0.18);
  }
  /* Front */
  .card-front {
    left: 78px; top: 35px; width: 587px; height: 362px;
    background: var(--white);
  }
  .card-front .bands { position: absolute; inset: 0; }
  .front-wordmark {
    position: absolute; left: 0; right: 0; top: 62px;
    text-align: center;
    font-size: 56px; font-weight: 400; letter-spacing: 0.5px;
    color: var(--purple);
  }
  .contact-list {
    position: absolute; right: 258px; top: 234px;
    list-style: none; color: var(--white);
    font-size: 16px; line-height: 24.5px; text-align: right;
  }
  .contact-list li { display: flex; justify-content: flex-end; align-items: center; gap: 12px; }
  .contact-list svg { width: 13px; height: 13px; flex: none; }
  .holder {
    position: absolute; left: 349px; top: 209px; color: var(--white);
  }
  .holder-name { font-size: 22px; font-weight: 600; line-height: 1.2; }
  .holder-role { font-size: 16px; line-height: 1.2; }
  .holder-company { font-size: 19px; font-weight: 600; margin-top: 21px; line-height: 1.2; }
  .holder-abn { font-size: 16px; line-height: 1.4; }
  .holder-abn b { font-weight: 600; }

  /* Back */
  .card-back {
    left: 389px; top: 505px; width: 566px; height: 352px;
    background: var(--purple); color: var(--white);
  }
  .headshot {
    position: absolute; left: 224px; top: 22px; width: 126px; height: 126px;
    border-radius: 50%;
    background: radial-gradient(circle at 50% 35%, var(--photo-light) 0%, #a3a8b4 55%, var(--photo-dark) 100%);
  }
  .back-wordmark {
    position: absolute; left: 0; right: 0; top: 166px;
    text-align: center; font-size: 52px; font-weight: 400; letter-spacing: 0.5px;
  }
  .services {
    position: absolute; left: 0; right: 0; top: 266px;
    text-align: center; font-size: 19px; font-weight: 600;
  }
  .services .sep { color: var(--orange); font-weight: 400; margin: 0 6px; }
  .services .accent { color: var(--orange); }
  .tagline {
    position: absolute; left: 0; right: 0; top: 304px;
    display: flex; align-items: center; gap: 18px;
    font-size: 18px; font-weight: 600;
  }
  .tagline::before, .tagline::after {
    content: ""; flex: 1; height: 1px; background: var(--white); opacity: 0.85;
  }
  .tagline::before { flex: 0 0 165px; }
</style>
</head>
<body>

  <section class="card card-front" aria-label="Business card front">
    <svg class="bands" viewBox="0 0 587 362" width="587" height="362" aria-hidden="true">
      <polygon points="0,202 388,202 415,165 587,165 587,362 0,362" fill="var(--purple)"/>
      <polygon points="0,173 402,173 383,199 0,199" fill="var(--orange)"/>
    </svg>
    <div class="front-wordmark">Calvanto Group</div>

    <ul class="contact-list">
      <li>0412 555 018
        <svg viewBox="0 0 16 16"><path fill="#fff" d="M3.5 1.5l2.6 0.3 1 3.1-1.6 1.2c0.8 1.7 2.2 3.1 3.9 3.9l1.2-1.6 3.1 1 0.3 2.6c-0.3 1.1-1.3 1.9-2.5 1.9C6 14 2 10 2 4c0-1.2 0.4-2.2 1.5-2.5z"/></svg>
      </li>
      <li>daniel.tran@calvanto.com.au
        <svg viewBox="0 0 16 16"><rect x="1" y="3" width="14" height="10" fill="#fff"/><path d="M1 3.5l7 5 7-5" fill="none" stroke="var(--purple)" stroke-width="1.3"/></svg>
      </li>
      <li>www.calvanto.com.au
        <svg viewBox="0 0 16 16"><circle cx="8" cy="8" r="7" fill="#fff"/><path d="M1 8h14M8 1c-3 3.5-3 10.5 0 14M8 1c3 3.5 3 10.5 0 14" fill="none" stroke="var(--purple)" stroke-width="1"/></svg>
      </li>
    </ul>

    <div class="holder">
      <div class="holder-name">Daniel Tran</div>
      <div class="holder-role">Director</div>
      <div class="holder-company">Calvanto Group</div>
      <div class="holder-abn"><b>ABN:</b> 52 418 903 276</div>
    </div>
  </section>

  <section class="card card-back" aria-label="Business card back">
    <div class="headshot" role="img" aria-label="Head shot photo of the director"></div>
    <div class="back-wordmark">Calvanto Group</div>
    <p class="services">Buy<span class="sep">|</span><span class="accent">Sell</span><span class="sep">|</span>Rent</p>
    <p class="tagline">let us show you property</p>
  </section>

</body>
</html>
```